Dynamic Business Card for Sports Supplements Company

Hi! I'm looking for an awesome business card to match my existing sports supplement company. I have uploaded my current company logo and screenshot of the front page of my website.

I would like to have something dynamic and interesting and utilize the colors in the website - the reds and purples

The business card should be double sided and focus on a unique eye-catching design on the back and include all the relevant company info.

Most importantly, it should say somewhere: "Sign up on our website for a coupon code."

Target Market(s)

Mostly for women gym goers but it shouldn't be too feminine. It should be in keeping with the website design. It should flow and clearly be connected to it

Industry/Entity Type

Business

Contact Information for Business Card

Lorraine K. Vestal
CEO
LVestal@Quorvanexco.com
www.quorvanexco.com
555.417.3820
P.O. Box 47315
Burke, Virginia 00000

Sign up on our website for a coupon code

Font styles to use
Serif
Sans Serif
Other font styles liked:
• Novecento font family and "Quorvanex" is in AR Destine font

Requirements
Must have
• One side should be a bold Quorvanex logo design. Even just the symbol itself may be o.k. (see attached file)

```html
<!DOCTYPE html>
<html lang="en">
<head>
<meta charset="utf-8">
<title>Quorvanex Business Card</title>
<link href="https://fonts.googleapis.com/css2?family=Open+Sans:wght@400;700;800&family=Oswald:wght@400;500&display=swap" rel="stylesheet">
<style>
  :root {
    --red: #e8222a;
    --white: #ffffff;
    --charcoal: #222222;
    --stage: #d4d4d4;
    --ink-light: #ffffff;
  }
  * { box-sizing: border-box; margin: 0; padding: 0; }
  html, body {
    width: 1200px; height: 1000px; overflow: hidden;
    background: var(--stage);
    font-family: "Open Sans", Arial, sans-serif;
  }
  .canvas {
    position: relative; width: 1200px; height: 1000px;
    display: flex; align-items: center; justify-content: center; gap: 40px;
  }
  .card {
    position: relative; width: 540px; height: 315px; overflow: hidden;
    box-shadow: 0 6px 18px rgba(0,0,0,0.25);
  }

  /* Front side */
  .card-front { background: var(--white); }
  .front-band {
    position: absolute; left: 0; right: 0; bottom: 0; height: 122px;
    background: var(--red);
  }
  .band-notch {
    position: absolute; left: 296px; top: -10px; width: 0; height: 0;
    border-left: 10px solid transparent; border-right: 10px solid transparent;
    border-bottom: 10px solid var(--red);
  }
  .front-wordmark {
    position: absolute; left: 95px; top: 78px;
    font-weight: 800; font-size: 38px; letter-spacing: 1px;
    color: var(--red); text-transform: uppercase;
  }
  .holder {
    position: absolute; right: 258px; top: 22px; text-align: right;
    color: var(--ink-light); line-height: 1.45;
  }
  .holder-name { font-weight: 700; font-size: 12px; text-transform: uppercase; letter-spacing: 0.3px; }
  .holder-title { font-size: 11px; }
  .holder-address { font-size: 11px; margin-top: 4px; }
  .band-divider {
    position: absolute; left: 298px; top: 20px; width: 1px; height: 70px;
    background: rgba(255,255,255,0.8);
  }
  .contact-list {
    position: absolute; left: 312px; top: 20px; list-style: none;
    color: var(--ink-light); font-size: 11px; line-height: 1.6;
  }
  .contact-list li { display: flex; align-items: center; gap: 8px; }
  .contact-list svg { width: 11px; height: 11px; flex: none; }

  /* Back side */
  .card-back { background: var(--charcoal); }
  .back-lockup {
    position: absolute; left: 0; right: 40px; top: 0; bottom: 0;
    display: flex; flex-direction: column; align-items: center; justify-content: center; gap: 18px;
  }
  .back-mark { width: 52px; height: 52px; background: var(--red); }
  .back-wordmark {
    font-weight: 800; font-size: 38px; letter-spacing: 1px;
    color: var(--white); text-transform: uppercase;
  }
  .coupon-note {
    position: absolute; right: 14px; top: 50%;
    transform: translate(50%, -50%) rotate(90deg);
    transform-origin: center; white-space: nowrap;
    margin-right: 8px;
    font-family: "Oswald", "Arial Narrow", sans-serif; font-weight: 500;
    font-size: 13px; letter-spacing: 1.6px; text-transform: uppercase;
    color: var(--white);
  }
</style>
</head>
<body>
<main class="canvas">

  <section class="card card-front" aria-label="Business card front">
    <div class="front-wordmark">Quorvanex</div>
    <div class="front-band">
      <span class="band-notch"></span>
      <div class="holder">
        <p class="holder-name">Lorraine K. Vestal</p>
        <p class="holder-title">CEO</p>
        <p class="holder-address">P.O. Box 47315 Burke, Virginia 00000</p>
      </div>
      <span class="band-divider"></span>
      <ul class="contact-list">
        <li>
          <svg viewBox="0 0 12 12" aria-hidden="true"><path fill="#fff" d="M2 1h3l1 3-1.5 1a7 7 0 0 0 2.5 2.5L8 6l3 1v3c0 .6-.4 1-1 1A9 9 0 0 1 1 2c0-.6.4-1 1-1z"/></svg>
          <span>555.417.3820</span>
        </li>
        <li>
          <svg viewBox="0 0 12 12" aria-hidden="true"><rect x="0.5" y="2" width="11" height="8" fill="#fff"/><path d="M0.5 2l5.5 4.5L11.5 2" fill="none" stroke="#e8222a" stroke-width="1"/></svg>
          <span>LVestal@Quorvanexco.com</span>
        </li>
        <li>
          <svg viewBox="0 0 12 12" aria-hidden="true"><circle cx="7" cy="5" r="3.5" fill="none" stroke="#fff" stroke-width="1.5"/><path d="M4.5 7.5L1 11" stroke="#fff" stroke-width="1.8"/></svg>
          <span>www.quorvanexco.com</span>
        </li>
      </ul>
    </div>
  </section>

  <section class="card card-back" aria-label="Business card back">
    <div class="back-lockup">
      <span class="back-mark"></span>
      <div class="back-wordmark">Quorvanex</div>
    </div>
    <p class="coupon-note">Sign up on our website for a coupon code</p>
  </section>

</main>
</body>
</html>
```